Moravel Aesthetic Doctor

I require an elegant, luxurious looking business card for my aesthetic business. I am a doctor and that will set me aside from competitors. I am planning to provide home and spa based treatments to clients with high expectations. I have attached my logo.

```html
<!DOCTYPE html>
<html lang="en">
<head>
<meta charset="utf-8">
<title>Moravel Aesthetic Doctor – Business Card</title>
<link rel="stylesheet" href="https://fonts.googleapis.com/css2?family=Roboto:wght@300;400;500&display=swap">
<style>
  :root {
    --page-bg: #e9e7e4;
    --card-grey: #a8aaac;
    --card-white: #ffffff;
    --brand-blue: #5bb8e6;
    --text-grey: #9b9d9f;
    --text-white: #ffffff;
    --mark-blue: #8fcdee;
  }
  * { box-sizing: border-box; margin: 0; padding: 0; }
  html, body {
    width: 1200px; height: 1200px; overflow: hidden;
    background: var(--page-bg);
    font-family: "Roboto", sans-serif;
  }
  .canvas {
    width: 1200px; height: 1200px;
    display: flex; flex-direction: column; align-items: center;
    justify-content: center; gap: 32px;
  }
  .card {
    width: 860px; height: 524px;
    border-radius: 4px;
    box-shadow: 0 6px 18px rgba(0,0,0,0.12);
    position: relative;
    display: flex; flex-direction: column; align-items: center;
  }
  .card--back { background: var(--card-grey); }
  .card--front { background: var(--card-white); }

  .brand {
    display: flex; align-items: center; gap: 26px;
    margin-top: 120px;
  }
  .card--front .brand { margin-top: 70px; }
  .brand__circle {
    width: 120px; height: 120px; border-radius: 50%;
    background: var(--mark-blue);
    flex: none;
  }
  .brand__name {
    font-weight: 300; line-height: 1;
    display: flex; flex-direction: column;
  }
  .brand__name .word { font-size: 84px; letter-spacing: 2px; }
  .brand__name .tag { font-size: 31px; letter-spacing: 3px; margin-top: 8px; }
  .card--back .brand__name { color: var(--text-white); }
  .card--front .brand__name { color: var(--text-grey); }

  .services {
    margin-top: 36px;
    color: var(--text-white);
    font-weight: 300; font-size: 25px; line-height: 1.35;
    text-align: center;
  }

  .person { margin-top: 34px; text-align: center; }
  .person__name {
    color: var(--brand-blue); font-weight: 500; font-size: 36px;
  }
  .person__name .letters { font-size: 20px; margin-left: 4px; }
  .person__title {
    color: var(--text-grey); font-weight: 300; font-size: 25px; margin-top: 6px;
  }

  .social { display: flex; gap: 20px; margin-top: 30px; }
  .social__dot {
    width: 32px; height: 32px; border-radius: 50%;
    background: var(--brand-blue);
  }

  .contacts {
    display: flex; gap: 40px; margin-top: 22px;
    color: var(--text-grey); font-weight: 300; font-size: 24px;
  }
  .contact { display: flex; align-items: center; gap: 10px; }
  .contact svg { width: 22px; height: 22px; flex: none; }
  .contact .accent { color: var(--brand-blue); }
</style>
</head>
<body>
<main class="canvas">
  <section class="card card--back" aria-label="Card back">
    <div class="brand">
      <div class="brand__circle"></div>
      <div class="brand__name">
        <span class="word">MORAVEL</span>
        <span class="tag">AESTHETIC DOCTOR</span>
      </div>
    </div>
    <p class="services">
      Dermal injectables • Plasma facials • Microneedling<br>
      Skin boosters • Excessive sweating<br>
      Home and Spa Based Treatments
    </p>
  </section>

  <section class="card card--front" aria-label="Card front">
    <div class="brand">
      <div class="brand__circle"></div>
      <div class="brand__name">
        <span class="word">MORAVEL</span>
        <span class="tag">AESTHETIC DOCTOR</span>
      </div>
    </div>
    <div class="person">
      <p class="person__name">Dr Lena Varga,<span class="letters">MRCPCH MD</span></p>
      <p class="person__title">Australasian Diploma of Aesthetic Medicine</p>
    </div>
    <div class="social">
      <span class="social__dot"></span>
      <span class="social__dot"></span>
    </div>
    <div class="contacts">
      <span class="contact">
        <svg viewBox="0 0 24 24" fill="#5bb8e6"><path d="M6.6 10.8a15.1 15.1 0 006.6 6.6l2.2-2.2a1 1 0 011-.25 11.4 11.4 0 003.6.57 1 1 0 011 1V20a1 1 0 01-1 1A17 17 0 013 4a1 1 0 011-1h3.5a1 1 0 011 1c0 1.25.2 2.45.57 3.57a1 1 0 01-.25 1z"/></svg>
        0800 555 019
      </span>
      <span class="contact">
        <svg viewBox="0 0 24 24" fill="none" stroke="#5bb8e6" stroke-width="2"><rect x="3" y="5" width="18" height="14" rx="1"/><path d="M3 6l9 7 9-7"/></svg>
        lena@moravel.co.nz
      </span>
      <span class="contact">
        <svg viewBox="0 0 24 24" fill="none" stroke="#5bb8e6" stroke-width="1.8"><circle cx="12" cy="12" r="9"/><ellipse cx="12" cy="12" rx="4" ry="9"/><path d="M3 12h18M5 7h14M5 17h14"/></svg>
        <span>www.<span class="accent">moravel</span>.co.nz</span>
      </span>
    </div>
  </section>
</main>
</body>
</html>
```